New Business Card Design Project LORVANTI-Italy

we are LORVANTI-Italy
our company in the market for 3 years we are luxury cosmetic company and its about time for a facelift :)
i will like to have elegant luxurious and unique business card
that will give the person that get it a unique, luxurious and elegant impression
I'm VERY OPEN FOR NEW IDEAS , even duo i add a few files of things that i see on line and i like them

i add my logo as well
my website is LORVANTI.COM
(if you would like to see the main style that we have)

Target Market(s)

adult that have money :)

Industry/Entity Type

Business

Contact Information for Business Card

Name - Dario Lorvanti
Position - CEO and CO Founder
address - 4817 E Halvern
telephone - 555-384-1926
email - dario@lorvanti.com
fax - 555-384-1926
website - LORVANTI.COM

Colors
000000
959595
fbee3e
ffffff

Requirements
Must have
• big logo in GOLD color
• elegant look
• impressive
Nice to have
• not must but maybe classy pattern background
• not must but maybe emblem
• maybe clear plastic business card
Should not have
• colors
• images

```html
<!DOCTYPE html>
<html lang="en">
<head>
<meta charset="utf-8">
<title>LORVANTI Italy – Business Card</title>
<link rel="stylesheet" href="https://fonts.googleapis.com/css2?family=Cinzel:wght@500&family=Open+Sans:wght@400;600;700&display=swap">
<style>
  :root {
    --backdrop: #2b2725;
    --card-black: #0d0d0d;
    --card-black-soft: #161616;
    --gold: #d9b64a;
    --gold-band: #dcbd58;
    --grey: #959595;
    --ink: #111111;
    --white: #ffffff;
  }
  * { margin: 0; padding: 0; box-sizing: border-box; }
  html, body { width: 1200px; height: 716px; overflow: hidden; }
  body {
    background: var(--backdrop);
    position: relative;
    font-family: "Open Sans", Arial, sans-serif;
  }
  .card {
    position: absolute;
    background: linear-gradient(160deg, var(--card-black-soft), var(--card-black));
    box-shadow: 0 14px 30px rgba(0,0,0,.55);
    overflow: hidden;
  }
  .card-front { left: 50px; top: 50px; width: 520px; height: 297px; }
  .card-back  { left: 610px; top: 360px; width: 540px; height: 308px; }

  .brand {
    position: absolute;
    display: flex; flex-direction: column; align-items: center;
    color: var(--gold);
    font-family: "Cinzel", "Times New Roman", serif;
    font-weight: 500;
  }
  .brand-dot {
    border: 2px solid var(--gold);
    border-radius: 50%;
  }
  .brand-name { letter-spacing: 1px; line-height: 1; }
  .brand-rule { height: 2px; background: var(--gold); }
  .brand-tag { letter-spacing: 3px; }

  .card-front .brand { left: 0; right: 0; top: 62px; }
  .card-front .brand-dot { width: 72px; height: 72px; margin-bottom: 14px; }
  .card-front .brand-name { font-size: 46px; }
  .card-front .brand-rule { width: 250px; margin-top: 8px; }
  .card-front .brand-tag { font-size: 14px; margin-top: 6px; }

  .card-back .brand { left: 120px; width: 230px; top: 26px; }
  .card-back .brand-dot { width: 50px; height: 50px; margin-bottom: 8px; }
  .card-back .brand-name { font-size: 33px; }
  .card-back .brand-rule { width: 190px; margin-top: 6px; }
  .card-back .brand-tag { font-size: 11px; margin-top: 4px; }

  .bands { position: absolute; inset: 0; width: 100%; height: 100%; }

  .holder { position: absolute; left: 24px; top: 144px; color: var(--white); }
  .holder-name { font-size: 15px; font-weight: 700; }
  .holder-role { font-size: 8px; color: #cfcfcf; margin-top: 1px; }

  .contact-list { position: absolute; list-style: none; color: var(--ink); font-weight: 600; }
  .contact-list li { display: flex; align-items: center; gap: 8px; line-height: 1.35; }
  .contact-list svg { width: 11px; height: 11px; fill: var(--ink); flex: none; }
  .contact-left { left: 24px; top: 188px; font-size: 12px; }
  .contact-right { left: 350px; top: 236px; font-size: 13px; font-weight: 700; }
  .contact-right .address { margin-top: 4px; font-size: 14px; }
</style>
</head>
<body>

  <section class="card card-front">
    <div class="brand">
      <span class="brand-dot"></span>
      <span class="brand-name">LORVANTI</span>
      <span class="brand-rule"></span>
      <span class="brand-tag">ITALY</span>
    </div>
  </section>

  <section class="card card-back">
    <svg class="bands" viewBox="0 0 540 308" preserveAspectRatio="none" aria-hidden="true">
      <rect x="0" y="168" width="540" height="140" fill="var(--gold-band)"/>
      <rect x="0" y="286" width="540" height="22" fill="var(--grey)"/>
      <polygon points="318,286 334,270 540,270 540,286" fill="var(--grey)"/>
      <line x1="24" y1="176" x2="300" y2="176" stroke="var(--gold)" stroke-width="0"/>
      <line x1="150" y1="166" x2="300" y2="166" stroke="var(--gold)" stroke-width="1.5"/>
    </svg>

    <div class="brand">
      <span class="brand-dot"></span>
      <span class="brand-name">LORVANTI</span>
      <span class="brand-rule"></span>
      <span class="brand-tag">ITALY</span>
    </div>

    <div class="holder">
      <p class="holder-name">Dario Lorvanti</p>
      <p class="holder-role">Position - CEO and CO Founder</p>
    </div>

    <ul class="contact-list contact-left">
      <li><svg viewBox="0 0 24 24"><path d="M6.6 10.8a15.1 15.1 0 0 0 6.6 6.6l2.2-2.2c.3-.3.7-.4 1-.2 1.1.4 2.3.6 3.6.6.6 0 1 .4 1 1V20c0 .6-.4 1-1 1A17 17 0 0 1 3 4c0-.6.4-1 1-1h3.5c.6 0 1 .4 1 1 0 1.3.2 2.5.6 3.6.1.3 0 .7-.2 1z"/></svg>555-384-1926</li>
      <li><svg viewBox="0 0 24 24"><path d="M2 5h20v14H2zm2 2v.5l8 5 8-5V7zm0 2.8V17h16V9.8l-8 5z"/></svg>dario@lorvanti.com</li>
    </ul>

    <ul class="contact-list contact-right">
      <li><svg viewBox="0 0 24 24"><path d="M6.6 10.8a15.1 15.1 0 0 0 6.6 6.6l2.2-2.2c.3-.3.7-.4 1-.2 1.1.4 2.3.6 3.6.6.6 0 1 .4 1 1V20c0 .6-.4 1-1 1A17 17 0 0 1 3 4c0-.6.4-1 1-1h3.5c.6 0 1 .4 1 1 0 1.3.2 2.5.6 3.6.1.3 0 .7-.2 1z"/></svg>555-384-1926</li>
      <li><svg viewBox="0 0 24 24"><path d="M12 2a10 10 0 1 0 0 20 10 10 0 0 0 0-20zm0 2c.9 0 2.3 1.8 2.8 5H9.2C9.7 5.8 11.1 4 12 4zM4.3 11h3c0 .7 0 1.4.1 2h-3a8 8 0 0 1-.1-2zm5 0h5.4a17 17 0 0 1 0 2H9.3a17 17 0 0 1 0-2zm7.4 0h3a8 8 0 0 1 0 2h-3l.1-2zM12 20c-.9 0-2.3-1.8-2.8-5h5.6c-.5 3.2-1.9 5-2.8 5z"/></svg>LORVANTI.COM</li>
      <li class="address"><svg viewBox="0 0 24 24"><path d="M12 2a7 7 0 0 0-7 7c0 5.2 7 13 7 13s7-7.8 7-13a7 7 0 0 0-7-7zm0 9.5A2.5 2.5 0 1 1 12 6.5a2.5 2.5 0 0 1 0 5z"/></svg>4817 E Halvern</li>
    </ul>
  </section>

</body>
</html>
```